Property management company looking for modern card design

We at Blue Heron Partners provides property management services for its residential and commercial properties, with expertise in all categories of multifamily, industrial and office projects throughout California.

We need a business card design that is professional and modern designed business card. In our field, clients get hundreds of business cards, we would like our card to stand out.

Please avoid small print.

Target Market(s)

Professionals and high end clients

Industry/Entity Type

Financial Planning

Contact Information for Business Card

Company Name: Blue Heron Partners, Name, email, license #, phone number, website blueheronpartners.com

Font styles to use
Sans Serif

Requirements
Must have
• The card design needs to be adaptable because there is a possibly we will be expanding into different sectors other than real estate. The card design should be focused on financial planning and asset management.
Nice to have
• Modern and simple business card. Eye catching. Non-standard size/shaped cards would be great.
• blueheronpartners.com
Should not have
• Too many bright color or any pictures or shapes of real estate stuff.

```html
<!DOCTYPE html>
<html lang="en">
<head>
<meta charset="utf-8">
<title>Blue Heron Partners – Business Card</title>
<link rel="stylesheet" href="https://fonts.googleapis.com/css2?family=Roboto:wght@400;500&family=Yesteryear&display=swap">
<style>
  :root {
    --page-bg: #d8d8d8;
    --card-dark: #333333;
    --card-light: #ffffff;
    --accent-gold: #b59c7f;
    --text-dark: #3a3a3a;
    --rule: #333333;
  }
  * { box-sizing: border-box; margin: 0; padding: 0; }
  html, body {
    width: 1200px;
    height: 1000px;
    overflow: hidden;
    background: var(--page-bg);
    font-family: "Roboto", Arial, sans-serif;
  }
  .canvas { position: relative; width: 1200px; height: 1000px; }

  .card {
    position: absolute;
    left: 288px;
    width: 626px;
    height: 358px;
    padding: 15px 15px;
  }
  .card-front { top: 140px; background: var(--card-light); }
  .card-back  { top: 531px; background: var(--card-dark); }

  .card-face {
    width: 100%;
    height: 100%;
    position: relative;
  }
  .card-front .card-face {
    background: var(--card-dark);
    display: flex;
    align-items: center;
    justify-content: center;
  }
  .company-name {
    color: var(--accent-gold);
    font-weight: 400;
    font-size: 42px;
    letter-spacing: 1px;
  }

  .card-back .card-face {
    background: var(--card-light);
    color: var(--text-dark);
    text-align: center;
  }
  .person-name {
    position: absolute;
    top: 88px;
    left: 0; right: 0;
    font-family: "Yesteryear", cursive;
    font-size: 40px;
    font-weight: 400;
    color: var(--accent-gold);
  }
  .license {
    position: absolute;
    top: 152px;
    left: 0; right: 0;
    font-size: 14px;
    letter-spacing: 0.3px;
  }
  .contact-row {
    position: absolute;
    top: 180px;
    left: 127px;
    width: 342px;
    height: 31px;
    border-top: 1px solid var(--rule);
    font-size: 14px;
  }
  .contact-divider {
    position: absolute;
    left: 137px;
    top: 0;
    width: 1px;
    height: 30px;
    background: var(--rule);
  }
  .contact-item { position: absolute; top: 9px; white-space: nowrap; }
  .contact-phone { left: -2px; }
  .contact-email { left: 148px; }
  .contact-label { color: var(--accent-gold); font-weight: 500; }
  .website {
    position: absolute;
    top: 225px;
    left: 0; right: 0;
    font-size: 14px;
    letter-spacing: 0.3px;
  }
</style>
</head>
<body>
  <main class="canvas">
    <section class="card card-front" aria-label="Card front">
      <div class="card-face">
        <h1 class="company-name">Blue Heron Partners</h1>
      </div>
    </section>

    <section class="card card-back" aria-label="Card back">
      <div class="card-face">
        <h2 class="person-name">Daniel Marsh</h2>
        <p class="license">License: #918273645</p>
        <div class="contact-row">
          <span class="contact-item contact-phone"><span class="contact-label">P</span> : 123-555-0190</span>
          <span class="contact-divider"></span>
          <span class="contact-item contact-email"><span class="contact-label">E</span> : info@blueheronpartners.com</span>
        </div>
        <p class="website">www.blueheronpartners.com</p>
      </div>
    </section>
  </main>
</body>
</html>
```